Meadowlight Soaps Business Card

The new business card design will incorporate my new logo components designed by one of your designers. Meadowlight Soaps creates high quality soaps and bath products. They would be suited for a Spa, Bed and Breakfast, Boutique environment. The look should be a white background.
Classy, soft and using the colour palet of the logo. The card will be two sided.

Reason: Need more time to make some changes and decide.

Target Market(s)

Looking to appeal to an upper end market. Spas, boutiques, independent gift stores, bridal salons, bed and breakfast, etc. I want the card to impart a sense of elegance, tranquility and Meadowlight. But also quality and value.

Industry/Entity Type

Business

Font styles to use
Sans Serif
Script

Requirements
Must have
• My logo on the front. But also on the back but faded out to allow written notes on the back.
On the front : Carol Pritchett
Owner/Creator
48 Fenwick Rd
Alderbrook, NS N4K 2P9
555.402.6183
Making Gentle Small-Batch Soaps And Bath Goods
Custom and Bulk Orders Gladly Taken
Www.meadowlightsoaps.ca
Www.facebook.com / MeadowlightSoapandBath
info@meadowlightsoaps.ca

```html
<!DOCTYPE html>
<html lang="en">
<head>
<meta charset="utf-8">
<title>Meadowlight Soaps Business Card</title>
<link href="https://fonts.googleapis.com/css2?family=Questrial&family=Poppins:wght@600&display=swap" rel="stylesheet">
<style>
  :root {
    --stage: #e9ecec;
    --card: #ffffff;
    --teal: #76a99b;
    --teal-soft: #93bdb1;
    --mint: #d6ece6;
    --mint-fade: #eef7f4;
    --blush: #ecd6c6;
    --grey: #c9cccb;
    --text-soft: #8a9a96;
  }
  * { box-sizing: border-box; margin: 0; padding: 0; }
  html, body { width: 1200px; height: 790px; overflow: hidden; }
  body {
    background: var(--stage);
    font-family: "Questrial", "Century Gothic", sans-serif;
    display: flex;
    align-items: center;
    justify-content: center;
    gap: 50px;
  }
  .card {
    position: relative;
    width: 540px;
    height: 309px;
    background: var(--card);
    box-shadow: 0 6px 22px rgba(0,0,0,0.14);
    overflow: hidden;
  }

  /* Back of card: faded logo area for notes */
  .card-back .speckle-field {
    position: absolute; inset: 0;
    background:
      radial-gradient(ellipse at 25% 45%, rgba(214,236,230,0.55), transparent 45%),
      radial-gradient(ellipse at 70% 30%, rgba(236,214,198,0.25), transparent 50%),
      radial-gradient(ellipse at 60% 75%, rgba(201,204,203,0.25), transparent 55%);
  }
  .card-back .logo-faded {
    position: absolute; left: 30px; top: 62px;
    width: 250px; text-align: center;
    opacity: 0.55;
  }

  /* Logo block (shared) */
  .logo-tree {
    display: block;
    margin: 0 auto;
    width: 130px; height: 130px;
    border-radius: 50% 50% 40% 40%;
    background: radial-gradient(ellipse at 50% 40%, var(--teal-soft) 0%, var(--mint) 45%, var(--blush) 70%, transparent 72%);
  }
  .logo-name {
    display: block;
    margin-top: 4px;
    font-size: 29px;
    line-height: 32px;
    color: var(--teal);
  }
  .logo-sub {
    display: block;
    font-size: 10px;
    letter-spacing: 4px;
    color: var(--teal);
  }

  /* Front of card */
  .card-front .band-accent {
    position: absolute; right: 0; top: 200px;
    width: 200px; height: 109px;
    background: linear-gradient(90deg, var(--mint-fade), var(--mint));
  }
  .card-front .tagline-band {
    position: absolute; left: 0; right: 0; bottom: 0;
    height: 62px;
    background: linear-gradient(90deg, var(--mint) 0%, var(--mint-fade) 100%);
    padding: 12px 0 0 30px;
    color: var(--teal);
    font-size: 14.5px;
    line-height: 19px;
  }
  .card-front .logo {
    position: absolute; right: 24px; top: 20px;
    width: 230px; text-align: center;
  }
  .card-front .logo-tree { width: 118px; height: 118px; }
  .contact {
    position: absolute; left: 30px; top: 56px;
    color: var(--text-soft);
  }
  .contact-name {
    font-family: "Poppins", "Century Gothic", sans-serif;
    font-weight: 600;
    font-size: 20px;
    color: var(--teal);
    line-height: 24px;
  }
  .contact-role { font-size: 14px; line-height: 17px; margin-bottom: 16px; }
  .contact-address { font-size: 14px; line-height: 19px; margin-bottom: 7px; }
  .contact-list { list-style: none; font-size: 14px; line-height: 20px; color: var(--teal); }
  .contact-list li { display: flex; align-items: center; gap: 7px; }
  .contact-list svg { width: 13px; height: 13px; fill: var(--text-soft); flex: none; }
  .social-dot { width: 11px; height: 11px; border-radius: 50%; background: var(--text-soft); margin: 0 1px; flex: none; }
</style>
</head>
<body>

  <section class="card card-back" aria-label="Back of card">
    <div class="speckle-field" role="img" aria-label="Soft scattered speckle pattern in mint, blush and grey"></div>
    <div class="logo-faded">
      <span class="logo-tree" role="img" aria-label="Faded tree illustration of the brand"></span>
      <span class="logo-name">Meadowlight</span>
      <span class="logo-sub">SOAPS</span>
    </div>
  </section>

  <section class="card card-front" aria-label="Front of card">
    <div class="band-accent" role="img" aria-label="Soft speckle pattern on mint band"></div>
    <div class="tagline-band">
      <p>Making Gentle Small-Batch Soaps And Bath Goods</p>
      <p>Custom and Bulk Orders Gladly Taken</p>
    </div>

    <div class="logo">
      <span class="logo-tree" role="img" aria-label="Tree illustration of the brand in teal and blush"></span>
      <span class="logo-name">Meadowlight</span>
      <span class="logo-sub">SOAPS</span>
    </div>

    <div class="contact">
      <h1 class="contact-name">Carol Pritchett</h1>
      <p class="contact-role">Owner/Creator</p>
      <p class="contact-address">48 Fenwick Rd<br>Alderbrook, NS N4K 2P9</p>
      <ul class="contact-list">
        <li><svg viewBox="0 0 16 16"><path d="M2 11c0-2 2-4 6-4s6 2 6 4v2H2z M1 6c2-3 12-3 14 0l-2 2h-2V6H5v2H3z"/></svg>555.402.6183</li>
        <li><svg viewBox="0 0 16 16"><path d="M1 3h14v10H1z M2 4.5v.5l6 4 6-4v-.5l-6 4z" fill-rule="evenodd"/></svg>info@meadowlightsoaps.ca</li>
        <li><svg viewBox="0 0 16 16"><circle cx="8" cy="8" r="7" fill="none" stroke="#8a9a96" stroke-width="1.4"/><path d="M1 8h14M8 1c-3 3-3 11 0 14M8 1c3 3 3 11 0 14" fill="none" stroke="#8a9a96" stroke-width="1.2"/></svg>www.meadowlightsoaps.ca</li>
        <li><span class="social-dot"></span>MeadowlightSoapandBath</li>
      </ul>
    </div>
  </section>

</body>
</html>
```